design a construction company business card

Design business card around our logo. Card must have all the typical info: name, title, address, phone, email, business name, etc. Somewhere on the card I would like to see our motto "Solid Foundations... Honest Work Every Time." Consider adding a splash of bright orange to the card to complement the blues and silvers/grays in the logo. We are open to metallic inks, textures, etc. We would like to see options on both light and dark backgrounds. The font in the logo is Euro Technic Extended Regular.

```html
<!DOCTYPE html>
<html lang="en">
<head>
<meta charset="utf-8">
<title>Hollis Contracting – Business Card</title>
<link rel="stylesheet" href="https://fonts.googleapis.com/css2?family=Aleo:wght@400;700&display=swap">
<style>
  :root {
    --page: #f7f7f7;
    --card: #0e1632;
    --blue: #2a7bc4;
    --blue-deep: #2b4aa6;
    --silver: #b7bac2;
    --white: #ffffff;
  }
  * { box-sizing: border-box; margin: 0; padding: 0; }
  html, body { width: 1200px; height: 754px; overflow: hidden; background: var(--page); }
  body { position: relative; font-family: "Aleo", Georgia, serif; }

  .card {
    position: absolute;
    top: 226px;
    height: 307px;
    background: var(--card);
    box-shadow: 0 14px 22px rgba(0,0,0,0.28);
    overflow: hidden;
  }
  .card--front { left: 50px; width: 540px; }
  .card--back { left: 621px; width: 537px; }

  .base-line {
    position: absolute;
    height: 7px;
    background: linear-gradient(90deg, var(--blue-deep), var(--blue));
  }

  /* Front */
  .brand {
    position: absolute;
    display: flex;
    align-items: center;
    gap: 10px;
    color: var(--blue);
    font-weight: 700;
    white-space: nowrap;
  }
  .brand__mark { width: 14px; height: 14px; background: var(--blue); flex: none; }
  .card--front .brand { left: 30px; top: 182px; font-size: 27px; letter-spacing: 0.5px; }
  .motto {
    position: absolute;
    left: 33px; top: 259px;
    font-size: 14.5px;
    color: var(--silver);
    white-space: nowrap;
  }
  .card--front .base-line { left: 25px; right: 0; top: 282px; }

  /* Back */
  .address {
    position: absolute;
    left: 27px; top: 52px;
    font-size: 14px;
    line-height: 22px;
    color: var(--blue);
  }
  .card--back .brand {
    right: 28px; top: 78px;
    font-size: 17px;
  }
  .contact-list {
    position: absolute;
    left: 116px; top: 170px;
    list-style: none;
  }
  .contact-list li {
    display: flex;
    align-items: center;
    gap: 7px;
    height: 22px;
    font-size: 14px;
    color: var(--white);
    white-space: nowrap;
  }
  .contact-list svg { width: 14px; height: 14px; fill: var(--blue); flex: none; }
  .person {
    position: absolute;
    right: 28px; top: 172px;
    text-align: right;
    white-space: nowrap;
  }
  .person__name { font-size: 20px; font-weight: 700; color: var(--blue); line-height: 24px; }
  .person__title { font-size: 12.5px; color: var(--white); }
  .edge-tab {
    position: absolute;
    right: 0; top: 174px;
    width: 12px; height: 32px;
    background: var(--blue);
  }
  .card--back .base-line { left: 69px; right: 0; top: 279px; }
</style>
</head>
<body>

<section class="card card--front" aria-label="Card front">
  <div class="brand"><span class="brand__mark"></span>HOLLIS CONTRACTING, INC.</div>
  <p class="motto">Solid Foundations... Honest Work Every Time</p>
  <div class="base-line"></div>
</section>

<section class="card card--back" aria-label="Card back">
  <p class="address">118/4 Ridge St, Lanefield<br>NSW 2190</p>
  <div class="brand"><span class="brand__mark"></span>HOLLIS CONTRACTING, INC.</div>

  <ul class="contact-list">
    <li>
      <svg viewBox="0 0 24 24" aria-hidden="true"><path d="M6.6 10.8a15.1 15.1 0 0 0 6.6 6.6l2.2-2.2c.3-.3.7-.4 1-.2 1.1.4 2.3.6 3.6.6.6 0 1 .4 1 1V20c0 .6-.4 1-1 1C10.6 21 3 13.4 3 4c0-.6.4-1 1-1h3.5c.6 0 1 .4 1 1 0 1.3.2 2.5.6 3.6.1.3 0 .7-.2 1z"/></svg>
      (02) 5550 1842
    </li>
    <li>
      <svg viewBox="0 0 24 24" aria-hidden="true"><path d="M7 1h10a2 2 0 0 1 2 2v18a2 2 0 0 1-2 2H7a2 2 0 0 1-2-2V3a2 2 0 0 1 2-2zm0 3v14h10V4zm5 15.5a1.2 1.2 0 1 0 0 2.4 1.2 1.2 0 0 0 0-2.4z"/></svg>
      0400 555 123
    </li>
    <li>
      <svg viewBox="0 0 24 24" aria-hidden="true"><path d="M2 5h20v14H2zm2 2v.6l8 5 8-5V7zm0 3v7h16v-7l-8 5z"/></svg>
      info@hollisbuild.com
    </li>
    <li>
      <svg viewBox="0 0 24 24" aria-hidden="true"><path d="M12 2a10 10 0 1 0 0 20 10 10 0 0 0 0-20zm6.9 6h-3a15.7 15.7 0 0 0-1.3-4A8 8 0 0 1 18.9 8zM12 4c.8 1.1 1.5 2.5 1.9 4h-3.8c.4-1.5 1.1-2.9 1.9-4zM4.3 14a8 8 0 0 1 0-4h3.4a16 16 0 0 0 0 4zm.8 2h3a15.7 15.7 0 0 0 1.3 4A8 8 0 0 1 5.1 16zm3-8h-3a8 8 0 0 1 4.3-4 15.7 15.7 0 0 0-1.3 4zM12 20c-.8-1.1-1.5-2.5-1.9-4h3.8c-.4 1.5-1.1 2.9-1.9 4zm2.3-6H9.7a14 14 0 0 1 0-4h4.6a14 14 0 0 1 0 4zm.3 6a15.7 15.7 0 0 0 1.3-4h3a8 8 0 0 1-4.3 4zm1.7-6a16 16 0 0 0 0-4h3.4a8 8 0 0 1 0 4z"/></svg>
      www.hollisbuild.com
    </li>
  </ul>

  <div class="person">
    <p class="person__name">Mark Delane</p>
    <p class="person__title">Founder | CEO</p>
  </div>
  <div class="edge-tab"></div>
  <div class="base-line"></div>
</section>

</body>
</html>
```